business card deign

Logo needs the following on it.
1. attached logo
2. Tagline - "If it keeps a drink cold or the party going...we do it!"
3. Name- Dalton Pikes, Founder and CPO
4. Address - 412 E. Carver Avenue, Ste 2207, Tampa, FL. 33917
5. Phone - 555.318.4726

```html
<!DOCTYPE html>
<html lang="en">
<head>
<meta charset="utf-8">
<title>Hoppen business card</title>
<link rel="stylesheet" href="https://fonts.googleapis.com/css2?family=Poppins:wght@300;400;600&display=swap">
<style>
  :root {
    --stage: #1b1b1d;
    --ink: #0b0b0c;
    --card-black: #111112;
    --paper: #ffffff;
    --silver: #a7a7aa;
    --foil: #cfcfd2;
  }
  * { margin: 0; padding: 0; box-sizing: border-box; }
  html, body {
    width: 1200px; height: 800px; overflow: hidden;
    background: var(--stage);
    font-family: "Poppins", sans-serif;
  }
  .stage {
    position: relative; width: 1200px; height: 800px;
    display: flex; align-items: center; justify-content: center; gap: 40px;
  }
  .card {
    position: relative; width: 540px; height: 310px;
    border-radius: 22px; overflow: hidden;
  }
  .card-front {
    background: var(--card-black);
    display: flex; flex-direction: column; align-items: center; justify-content: center;
  }
  .brand {
    display: flex; align-items: center; gap: 14px;
    font-weight: 600; letter-spacing: 0.22em;
  }
  .brand-dot { width: 18px; height: 18px; border-radius: 50%; }
  .card-front .brand { color: var(--foil); font-size: 40px; }
  .card-front .brand-dot { background: var(--foil); }
  .tagline {
    margin-top: 34px; color: var(--foil);
    font-weight: 300; font-size: 14px; letter-spacing: 0.02em;
  }
  .card-back { background: var(--paper); }
  .card-back .wave { position: absolute; inset: 0; width: 100%; height: 100%; }
  .card-back .brand {
    position: absolute; top: 36px; right: 60px;
    color: var(--ink); font-size: 30px;
  }
  .card-back .brand-dot { background: var(--ink); width: 14px; height: 14px; }
  .contact {
    position: absolute; left: 40px; bottom: 22px;
    color: var(--paper); font-size: 14px; line-height: 1.35;
  }
  .contact-name { font-weight: 600; font-size: 21px; line-height: 1.2; }
  .contact-role { font-weight: 400; font-size: 15px; margin-bottom: 8px; }
  .contact-phone { margin-top: 6px; }
  .contact-phone b { font-weight: 600; }
</style>
</head>
<body>
<main class="stage">
  <section class="card card-front">
    <div class="brand"><span class="brand-dot"></span><span>HOPPEN</span></div>
    <p class="tagline">If it keeps a drink cold or the party going...we do it!</p>
  </section>

  <section class="card card-back">
    <svg class="wave" viewBox="0 0 540 310" preserveAspectRatio="none" aria-hidden="true">
      <path d="M0 66 C 150 86, 380 141, 470 116 C 520 101, 540 46, 540 -14 L540 310 L0 310 Z" fill="#a7a7aa"/>
      <path d="M0 74 C 150 94, 380 149, 470 124 C 520 109, 540 54, 540 -6 L540 310 L0 310 Z" fill="#ffffff"/>
      <path d="M0 80 C 150 100, 380 155, 470 130 C 520 115, 540 60, 540 0 L540 310 L0 310 Z" fill="#111112"/>
    </svg>
    <div class="brand"><span class="brand-dot"></span><span>HOPPEN</span></div>
    <div class="contact">
      <p class="contact-name">Dalton Pikes</p>
      <p class="contact-role">Founder and CPO</p>
      <p>412 E. Carver Avenue,<br>Ste 2207, Tampa,<br>FL. 33917</p>
      <p class="contact-phone"><b>P :</b> 555.318.4726</p>
    </div>
  </section>
</main>
</body>
</html>
```